Real Estate investment company needs billboard designs

This is our website: https://brightlanepropertygroup.com/
We are looking for some billboard concepts that uses our CEO in the design. I have attached some images and 1 billboard design that someone in our industry uses, but we don't want it exactly like his.

Industry/Entity Type

real estate

Colors

Designer to choose colors to be used in the design.

Requirements
Must have
• Company colors from websiute

```html
<!DOCTYPE html>
<html lang="en">
<head>
<meta charset="utf-8">
<title>Brightlane Property Group Billboard</title>
<link rel="stylesheet" href="https://fonts.googleapis.com/css2?family=Montserrat:wght@600;800;900&family=Oswald:wght@600&display=swap">
<style>
  :root {
    --deep: #0f3b4a;
    --deep-dark: #0a2c38;
    --amber: #f2a541;
    --cream: #fdf6ea;
    --white: #ffffff;
    --backdrop: #eef1f4;
    --photo-top: #5d7a84;
    --photo-bottom: #1f4a57;
  }
  * { margin: 0; padding: 0; box-sizing: border-box; }
  html, body { width: 1200px; height: 857px; overflow: hidden; background: var(--backdrop); }
  .canvas { position: relative; width: 1200px; height: 857px; }
  .billboard {
    position: absolute; left: 20px; top: 148px;
    width: 1160px; height: 560px;
    background: var(--deep);
    overflow: hidden;
    box-shadow: 0 6px 24px rgba(0,0,0,0.15);
  }
  .ceo-photo {
    position: absolute; left: 0; top: 0;
    width: 440px; height: 560px;
    background: linear-gradient(180deg, var(--photo-top), var(--photo-bottom));
    clip-path: polygon(0 0, 100% 0, 82% 100%, 0 100%);
  }
  .accent-stripe {
    position: absolute; left: 0; top: 0;
    width: 470px; height: 560px;
    background: var(--amber);
    clip-path: polygon(94% 0, 100% 0, 82% 100%, 76% 100%);
  }
  .content { position: absolute; left: 480px; top: 0; width: 640px; height: 560px; }
  .brand {
    position: absolute; left: 0; top: 40px;
    display: flex; align-items: center; gap: 14px;
  }
  .brand-mark { width: 26px; height: 26px; background: var(--amber); }
  .brand-name {
    font-family: 'Montserrat', sans-serif; font-weight: 800;
    color: var(--white); font-size: 26px; line-height: 1;
    text-transform: uppercase; letter-spacing: 1.5px;
  }
  .headline {
    position: absolute; left: 0; top: 108px; width: 640px;
    font-family: 'Montserrat', sans-serif; font-weight: 900;
    font-size: 68px; line-height: 1.08;
    color: var(--white);
  }
  .headline .accent { color: var(--amber); }
  .tagline {
    position: absolute; left: 0; top: 294px; width: 640px;
    font-family: 'Oswald', sans-serif; font-weight: 600;
    color: var(--cream); font-size: 36px; line-height: 1.2;
    letter-spacing: 0.5px;
  }
  .contact-bar {
    position: absolute; left: 0; bottom: 0;
    width: 1160px; height: 118px;
    background: var(--amber);
    clip-path: polygon(0 0, 100% 0, 100% 100%, 0 100%);
  }
  .contact {
    position: absolute; left: 480px; bottom: 18px;
    display: flex; flex-direction: column; gap: 6px;
    font-family: 'Montserrat', sans-serif; color: var(--deep-dark);
  }
  .phone { display: flex; align-items: center; gap: 14px; }
  .phone-icon { width: 42px; height: 42px; flex: none; }
  .phone-label { font-weight: 800; font-size: 22px; letter-spacing: 2px; }
  .phone-number { font-weight: 900; font-size: 44px; line-height: 1; }
  .website {
    font-weight: 800; font-size: 22px; letter-spacing: 1px;
    color: var(--deep-dark); text-decoration: none; text-transform: uppercase;
  }
</style>
</head>
<body>
<div class="canvas">
  <div class="billboard">
    <div class="contact-bar"></div>
    <div class="accent-stripe"></div>
    <div class="ceo-photo" role="img" aria-label="Photo of the company CEO, smiling and gesturing toward the headline"></div>

    <div class="content">
      <div class="brand">
        <div class="brand-mark"></div>
        <div class="brand-name">Brightlane Property Group</div>
      </div>

      <h1 class="headline">Ready to sell?<br><span class="accent">We buy as-is.</span></h1>

      <p class="tagline">Fair cash offer within 24 hours.<br>No repairs. No fees.</p>
    </div>

    <div class="contact">
      <div class="phone">
        <svg class="phone-icon" viewBox="0 0 46 46" aria-hidden="true">
          <circle cx="23" cy="23" r="23" fill="var(--deep-dark)"/>
          <path d="M16 11c1.2-.6 2.4 0 3 1.2l2 4.2c.5 1 .2 2.2-.7 2.9l-1.6 1.2c1 2.6 3.2 4.8 5.8 5.8l1.2-1.6c.7-.9 1.9-1.2 2.9-.7l4.2 2c1.2.6 1.8 1.8 1.2 3-.9 2.4-3.2 4-5.8 3.6C19.8 31.8 14.2 26.2 12.4 17.8 12 15.2 13.6 12 16 11z" fill="var(--amber)"/>
        </svg>
        <span class="phone-label">CALL</span>
        <span class="phone-number">865-555-0142</span>
      </div>
      <a class="website" href="https://brightlanepropertygroup.com/">brightlanepropertygroup.com</a>
    </div>
  </div>
</div>
</body>
</html>
```